A website where experts collaborate on your project

I am building a new website where experts (yes, like designers) collaborate on projects with the project owner. More minds = more collaboration = better end product. Please see Pelmora(dot)com for a quick landing page I created for collaborating on presentations (although there will be many project types offered)

I am looking for a DESIGNER LONG TERM, but for now, just need initial mock ups to show the web programmers.

I have 21 Word documents loosely designed, what I would like to see here is a theme. Please DO NOT GO OFF WHAT YOU CURRENTLY SEE AT PELMORA. What is up now is only a quick landing page.

You can view a Word doc of the homepage here:
https://www.filevanta.com/s/qx83kdm2/home.docx?dl=0

WHAT AM I LOOKING FOR?
A clean, well designed theme.

Here is a link to the logo:
https://www.filevanta.com/s/mr47tpz9/logo%20-%20horizontal.tif?dl=0
-----------------------------------------
Here are a few sites I like the design of and what I like about them:
www.quenbrook.com-all around my favorite, beautiful graphics, clean layout, bold use of colors on a dark background
Ravelto.com- clean layout, The use of humans and bubble style elements.
Mintharbor.com :) clean, bold, unique pop art style but professional
plumevault.com - From the unique colors and artwork and the ability of that art to not interfere with the important elements of the site
sparkwidgets.com-clean, nice colors, well organized and separated sections.
www.dunmereco.com-love the font, use of colors and sectionalized style

All in all, I am not picky and open to so many styles. I would ultimately like the designer I pick to design all 21 pages.
Updates

Hello everyone,Moving forward, I would like you all to pay special attention to the section in my brief titled "Here are a few sites I like the design of and what I like about them". Please see below, I handpicked each one of these as sites I really like. Thank you.Here are a few sites I like the design of and what I like about them:Ravelto.com- clean layout, The use of humans and bubble style elements.Mintharbor.com :) clean, bold, unique pop art style but professionalwriteraccess.com - From the unique colors and artwork and the ability of that art to not interfere with the important elements of the sitegrowthgeeks.com-clean, nice colors, well organized and separated sections.www.dunmereco.com-love the font, use of colors and sectionalized stylewww.quenbrook.com-beautiful graphics, clean layout, bold use of colors----------------------------------------- Added Tuesday, November 24, 2015

I updated the homepage, you can see it here:https://www.dropbox.com/s/kwlkbsookq3cg2m/1new%20homepage.docx?dl=0I am modeling it after my favorite designed site: triplelift.comI love the dark colors with the orange glowing style boldness of the buttons. It's real clean too. Added Tuesday, November 24, 2015

Target Market(s)

small business owners, marketers, freelancer writers, graphic designers,

Industry/Entity Type

Building

Number of Pages Required

5+ page

Requirements
Must have
• I can't think of anything the project must have.
Nice to have
• WHAT AM I LOOKING FOR?
• A clean, well designed theme. I had a designer do a bit of work putting elements together, I found it to be very plain, but I like the Application Page (https://www.filevanta.com/s/jb19ckr3/Pelmora-Website.ai?dl=0)
• Here is a link to the logo:
• https://www.filevanta.com/s/mr47tpz9/logo%20-%20horizontal.tif?dl=0
• Here are a few sites I like the design of and what I like about them:
• Ravelto.com- clean layout, The use of humans and bubble style elements.
• Mintharbor.com :) clean, bold, unique pop art style but professional
• plumevault.com - From the unique colors and artwork and the ability of that art to not interfere with the important elements of the site
• sparkwidgets.com-clean, nice colors, well organized and separated sections.
• www.dunmereco.com-love the font, use of colors and sectionalized style
• www.quenbrook.com-beautiful graphics, clean layout, bold use of colors
• -----------------------------------------
Should not have
• out of the boxed, templated style website. I want this site to be memorable and not look like a thousand others

```html
<!DOCTYPE html>
<html lang="en">
<head>
<meta charset="utf-8">
<title>Pelmora — Convert More Customers</title>
<link href="https://fonts.googleapis.com/css2?family=Raleway:wght@400;500;600;700;800&display=swap" rel="stylesheet">
<style>
:root{
  --orange:#f7931e;
  --orange-dark:#e07d0c;
  --cyan:#1ba6d9;
  --ink:#222222;
  --topbar:#3b3b3b;
  --text:#333333;
  --muted:#777777;
  --line:#dddddd;
  --white:#ffffff;
}
*{box-sizing:border-box;margin:0;padding:0}
html,body{width:805px;height:1200px;overflow:hidden}
body{font-family:"Raleway",Arial,sans-serif;color:var(--text);background:var(--white);position:relative;font-size:11px}
.abs{position:absolute}

/* top bar */
.topbar{left:0;top:0;width:805px;height:21px;background:var(--topbar);color:var(--white);font-size:9.5px}
.topbar .mail{left:501px;top:5px;display:flex;align-items:center;gap:6px}
.topbar .lang{left:659px;top:4px;display:flex;gap:8px}

/* header */
.header{left:0;top:21px;width:805px;height:77px;background:var(--white)}
.brand{left:66px;top:25px;display:flex;align-items:center;gap:10px}
.brand-name{font-size:24px;font-weight:700;color:var(--orange);letter-spacing:.2px}
.brand-dot{width:38px;height:38px;border-radius:50%;background:var(--orange)}
.btn-outline{left:573px;top:30px;width:79px;height:22px;border:1px solid #bbb;font-size:10px;display:flex;align-items:center;justify-content:center;color:#444}
.btn-cyan{left:659px;top:30px;width:79px;height:22px;background:var(--cyan);color:var(--white);font-size:10px;display:flex;align-items:center;justify-content:center}

/* nav */
.nav{left:0;top:98px;width:805px;height:36px;background:var(--orange)}
.browse{left:66px;top:8px;width:124px;height:20px;background:var(--white);font-size:9.5px;color:#555;padding:0 6px;display:flex;align-items:center;justify-content:space-between}
.nav-links{right:67px;top:11px;display:flex;gap:31px;color:var(--white);font-size:11px}

/* hero */
.hero{left:0;top:134px;width:805px;height:311px;background:linear-gradient(90deg,#5d6468 0%,#7c8387 45%,#8f8a84 70%,#6b6f72 100%)}
.hero-mark{left:70px;top:63px;width:42px;height:38px;border-radius:50%;border:3px solid var(--white)}
.hero h1{left:66px;top:117px;font-size:25px;font-weight:800;color:var(--white);letter-spacing:.2px}
.hero p{left:66px;top:155px;width:290px;font-size:12.3px;line-height:20px;color:var(--white)}
.btn-orange{background:linear-gradient(#faa43a,var(--orange-dark));color:var(--white);font-weight:700;display:flex;align-items:center;justify-content:center;border-radius:2px}
.hero .cta{left:66px;top:210px;width:83px;height:27px;font-size:10px}
.dots{left:376px;top:292px;display:flex;gap:14px}
.dots span{width:8px;height:8px;border-radius:50%;background:#ddd}
.dots span.on{background:transparent;border:1.5px solid #eee;box-shadow:inset 0 0 0 1.5px #777;}

/* sidebar */
.sidebar{left:66px;top:455px;width:163px;height:429px;border:1px solid var(--line)}
.bar-dark{background:var(--ink);color:var(--white);font-size:10.5px;font-weight:500;display:flex;align-items:center;padding:0 8px}
.sidebar .bar-dark{left:7px;top:11px;width:146px;height:23px}
.filter-title{left:7px;top:48px;font-size:9.5px;font-weight:700;color:var(--ink)}
.filter-rule{left:7px;top:63px;width:51px;height:1px;background:#888}
.slider{left:7px;top:97px;width:136px;height:2px;background:#ccc}
.slider .fill{left:4px;top:0;width:87px;height:2px;background:var(--ink)}
.slider .knob{top:-3px;width:8px;height:8px;border-radius:50%;background:var(--ink)}
.filter-now{left:7px;top:119px;width:67px;height:20px;font-size:8px;letter-spacing:.3px}
.price{left:82px;top:124px;font-size:10px;color:var(--muted)}
.price b{color:var(--ink);font-weight:600}
.filters{left:7px;top:164px;width:146px;list-style:none}
.filters li{height:23px;border-bottom:1px solid var(--line);display:flex;align-items:center;justify-content:space-between;font-size:9.5px;color:#333}
.filters li::after{content:"";border:3px solid transparent;border-top:4px solid #333;margin-top:4px;margin-right:4px}
.save{left:8px;top:338px;width:67px;height:23px;font-size:8.5px}

/* projects */
.projects{left:251px;top:467px;width:487px}
.projects .bar-dark{left:0;top:0;width:487px;height:22px;font-size:11px;justify-content:space-between}
.sort{display:flex;align-items:center;gap:8px;font-size:9.5px}
.select{width:73px;height:15px;background:var(--white);color:#777;font-size:8.5px;padding:0 5px;display:flex;align-items:center;justify-content:space-between}
.select::after{content:"";border:3px solid transparent;border-top:4px solid #333;margin-top:4px}
.timer{margin-left:6px;font-size:8.5px}
.project{left:0;width:487px;height:70px;display:flex;align-items:center;padding-left:14px;gap:12px}
.project.featured{border:2px solid var(--orange)}
.project:not(.featured){border-bottom:1px dashed #ccc}
.project .icon{width:30px;height:30px;border-radius:50%;border:3px solid #444}
.project.featured .icon{border-color:var(--orange)}
.project h3{font-size:11.3px;font-weight:500;color:#333;margin-bottom:8px}
.project .meta{font-size:11px;color:#333}
.project .meta .hl{color:var(--orange)}

/* testimonials */
.testimonials{left:0;top:918px;width:805px;height:152px;background:linear-gradient(90deg,#5f6264,#787a7b 50%,#6c6e70);color:var(--white);text-align:center}
.testimonials h2{left:0;top:18px;width:805px;font-size:16px;font-weight:700}
.testimonials .rule{left:385px;top:41px;width:35px;height:1px;background:var(--white)}
.quote{left:150px;top:59px;width:505px;font-size:11.3px;line-height:18px}
.qmark{font-size:26px;font-weight:800;color:var(--orange);line-height:1}
.q-open{left:123px;top:54px}
.q-close{left:657px;top:80px}
.author{left:0;top:116px;width:805px;display:flex;justify-content:center;align-items:center;gap:10px;font-size:12.5px}
.author small{font-size:9.5px}
.arrow-l{border:5px solid transparent;border-right:8px solid var(--white);margin-right:8px}
.arrow-r{border:5px solid transparent;border-left:8px solid var(--orange);margin-left:6px}

/* footer */
.footer{left:0;top:1070px;width:805px;height:101px;background:var(--ink);color:var(--white)}
.footer-links{left:0;top:24px;width:805px;display:flex;justify-content:center;font-size:11px}
.footer-links span{padding:0 15px;border-left:1px solid #666}
.footer-links span:first-child{border-left:none}
.social{left:0;top:59px;width:805px;display:flex;justify-content:center;gap:15px}
.social span{width:20px;height:20px;border-radius:50%}
.legal{left:0;top:1171px;width:805px;height:29px;background:var(--orange);color:var(--white);font-size:9px;display:flex;align-items:center;justify-content:center;gap:7px}
.legal .dot{width:16px;height:16px;border-radius:50%;border:2px solid var(--white)}
</style>
</head>
<body>

<div class="abs topbar">
  <div class="abs mail">
    <svg width="10" height="8" viewBox="0 0 10 8"><rect x="0" y="0" width="10" height="8" fill="#fff"/><path d="M0 0 L5 4.5 L10 0" stroke="#3b3b3b" stroke-width="1.2" fill="none"/></svg>
    email@pelmora.com
  </div>
  <div class="abs lang">Select Language <span>▼</span></div>
</div>

<header class="abs header">
  <div class="abs brand"><span class="brand-name">Pelmora</span><span class="brand-dot"></span></div>
  <div class="abs btn-outline">News Feeds</div>
  <div class="abs btn-cyan">Notifications</div>
</header>

<nav class="abs nav">
  <div class="abs browse">Browse <span>▾</span></div>
  <div class="abs nav-links"><span>Home</span><span>Projects</span><span>How it Works</span><span>Plans</span><span>My Account</span></div>
</nav>

<section class="abs hero" role="img" aria-label="Photo of two business colleagues reviewing a tablet outside an office building">
  <div class="abs hero-mark"></div>
  <h1 class="abs">CONVERT MORE CUSTOMERS</h1>
  <p class="abs">Experience the power of experts collaborating on your project.</p>
  <div class="abs btn-orange cta">GET STARTED</div>
  <div class="abs dots"><span></span><span></span><span class="on"></span></div>
</section>

<aside class="abs sidebar">
  <div class="abs bar-dark">CATEGORIES</div>
  <div class="abs filter-title">FILTER BY PRICE</div>
  <div class="abs filter-rule"></div>
  <div class="abs slider">
    <div class="abs fill"></div>
    <div class="abs knob" style="left:0"></div>
    <div class="abs knob" style="left:87px"></div>
  </div>
  <div class="abs bar-dark filter-now">FILTER NOW</div>
  <div class="abs price">Price: <b>$0 - $300</b></div>
  <ul class="abs filters">
    <li>Country</li><li>Categories</li><li>Time Left</li><li>Active | Expired</li>
    <li>Contains adult content</li><li>keywords</li><li>followers</li>
  </ul>
  <div class="abs btn-orange save">SAVE FILTER</div>
</aside>

<main class="abs projects">
  <div class="abs bar-dark">
    <span>Crowd Projects:</span>
    <div class="sort">Sort: <span class="select">Price</span><span class="select">Country</span><span class="timer">05h : 25m : 06s</span></div>
  </div>
  <article class="abs project featured" style="top:48px">
    <span class="icon"></span>
    <div><h3>Morbi in ante arcu. Maecenas sit amet sem vel</h3><div class="meta"><span class="hl">$ 80</span>, U.K., <span class="hl">TIME LEFT:</span> 6 days</div></div>
  </article>
  <article class="abs project" style="top:123px">
    <span class="icon"></span>
    <div><h3>Lorem ipsum dolor sit amet, consectetur adipiscing</h3><div class="meta"><span class="hl">$ 90</span>, U.K., <span class="hl">TIME LEFT:</span> 6 days</div></div>
  </article>
  <article class="abs project" style="top:198px">
    <span class="icon"></span>
    <div><h3>Neque porro quisquam est qui dolorem ipsum</h3><div class="meta"><span class="hl">$ 250</span>, U.K., <span class="hl">TIME LEFT:</span> 6 days</div></div>
  </article>
  <article class="abs project" style="top:273px">
    <span class="icon"></span>
    <div><h3>Duis ligula sapien, sodales id tortor vitae, ornare</h3><div class="meta"><span class="hl">$ 62</span>, U.K., <span class="hl">TIME LEFT:</span> 6 days</div></div>
  </article>
  <article class="abs project" style="top:348px">
    <span class="icon"></span>
    <div><h3>Neque porro quisquam est qui dolorem ipsum</h3><div class="meta"><span class="hl">$ 48</span>, U.K., <span class="hl">TIME LEFT:</span> 6 days</div></div>
  </article>
</main>

<section class="abs testimonials" role="img" aria-label="Dimmed photo of colleagues smiling in a meeting behind the testimonial">
  <h2 class="abs">TESTIMONIALS</h2>
  <div class="abs rule"></div>
  <span class="abs qmark q-open">“</span>
  <p class="abs quote">"With Pelmora I have multiple experts perfecting my content and I only pay for the feedback I find valuable. It's perfect"</p>
  <span class="abs qmark q-close">”</span>
  <div class="abs author"><span class="arrow-l"></span>Dale Marsh <small>- CEO</small><span class="arrow-r"></span></div>
</section>

<footer class="abs footer">
  <div class="abs footer-links"><span>Home</span><span>Projects</span><span>How it Works</span><span>Plans</span><span>My Account</span></div>
  <div class="abs social">
    <span style="background:#3b5a9a"></span><span style="background:#dd4b39"></span><span style="background:#1da1f2"></span><span style="background:#517fa4"></span>
  </div>
</footer>
<div class="abs legal"><span class="dot"></span>Copyrights 2015. Pelmora. All rights reserved</div>

</body>
</html>
```